Bright Harbor Counseling Letterhead for hip modern business

I would like some ombre use of the colors in the logo hip letterhead that incorporates logo colors and feel, needs to connect with young professionals and college students. i need to be able to write letters to schools to excuse absences as well. i like color blocks on one side preferably using colors from the attached logo design.

Target Market(s)

high income young people, young adults and college students

Industry/Entity Type

mental health

Font styles to use
Serif
Sans Serif

Colors
0054AA
0677BA
7BADD7
CADEEF
E8F1F8
0094D4
00A9DD
6FCCEA
C7EBF8
E9F6FB
00AB8E
00BBA5
67D7C9
C6EFE9
E9F9F6
59FF00
82FF00
B8FF75
E3FFCB
F4FFEA
A7469A
B969AE
D3A5CF
EDDBEB
F8F0F9
6B429C
8869AF
B7A5CE
E3DAEB
F3F0F8

Requirements
Must have
• a modern hip feel, somewhat color

```html
<!DOCTYPE html>
<html lang="en">
<head>
<meta charset="utf-8">
<title>Bright Harbor Counseling — Letterhead</title>
<link rel="stylesheet" href="https://fonts.googleapis.com/css2?family=Nunito+Sans:wght@300;400&display=swap">
<style>
  :root {
    --backdrop: #2f2f2f;
    --paper: #ffffff;
    --ink: #2b2b2b;
    --ink-soft: #444444;
    --teal: #4fc3b5;
    --blue: #2f72ba;
    --indigo: #5a63b4;
    --purple: #8a4398;
    --sky: #6fcce9;
    --white: #ffffff;
  }
  * { box-sizing: border-box; margin: 0; padding: 0; }
  html, body {
    width: 1200px;
    height: 1064px;
    overflow: hidden;
    background: var(--backdrop);
    font-family: "Nunito Sans", sans-serif;
  }
  .letterhead {
    position: absolute;
    left: 229px;
    top: 52px;
    width: 742px;
    height: 960px;
    background: var(--paper);
    overflow: hidden;
  }
  .brand {
    position: absolute;
    left: 62px;
    top: 58px;
    display: flex;
    align-items: flex-start;
    gap: 10px;
    color: var(--ink);
    font-weight: 300;
  }
  .brand-dot {
    width: 26px;
    height: 26px;
    border-radius: 50%;
    background: var(--purple);
    margin-top: 4px;
  }
  .brand-name {
    display: flex;
    flex-direction: column;
    align-items: flex-end;
    line-height: 1;
  }
  .brand-name .primary { font-size: 30px; letter-spacing: 0.5px; }
  .brand-name .secondary { font-size: 13px; letter-spacing: 3px; margin-top: 4px; }

  .contact-list {
    position: absolute;
    left: 488px;
    top: 36px;
    list-style: none;
    font-size: 10.5px;
    color: var(--ink-soft);
  }
  .contact-list li {
    display: flex;
    align-items: center;
    gap: 6px;
    height: 15px;
  }
  .contact-icon { width: 11px; height: 11px; flex: none; }

  .footer-swoosh {
    position: absolute;
    left: 0;
    top: 0;
    width: 742px;
    height: 960px;
  }
  .footer-address {
    position: absolute;
    right: 28px;
    bottom: 30px;
    display: flex;
    align-items: center;
    gap: 7px;
    font-size: 11.5px;
    color: var(--white);
    letter-spacing: 0.2px;
  }
</style>
</head>
<body>
  <main class="letterhead">
    <svg class="footer-swoosh" viewBox="0 0 742 960" aria-hidden="true">
      <defs>
        <linearGradient id="band-gradient" x1="0" y1="0" x2="1" y2="0">
          <stop offset="0" stop-color="var(--blue)"/>
          <stop offset="0.5" stop-color="var(--indigo)"/>
          <stop offset="1" stop-color="var(--purple)"/>
        </linearGradient>
      </defs>
      <path class="accent-stripe" d="M -10 928 Q 420 878 742 676" fill="none" stroke="var(--teal)" stroke-width="11"/>
      <path class="color-band" d="M 0 960 L 0 952 Q 440 912 742 712 L 742 960 Z" fill="url(#band-gradient)"/>
    </svg>

    <header class="brand">
      <span class="brand-dot"></span>
      <div class="brand-name">
        <span class="primary">Bright Harbor</span>
        <span class="secondary">Counseling</span>
      </div>
    </header>

    <ul class="contact-list">
      <li>
        <svg class="contact-icon" viewBox="0 0 12 12"><circle cx="6" cy="6" r="6" fill="var(--teal)"/><path d="M4 3.2 L5 4.6 L4.4 5.3 Q5.2 6.9 6.7 7.6 L7.4 7 L8.8 8 L8.2 8.9 Q5 8.6 3.2 4 Z" fill="var(--white)"/></svg>
        <span>(555) 014-2280</span>
      </li>
      <li>
        <svg class="contact-icon" viewBox="0 0 12 12"><circle cx="6" cy="6" r="6" fill="var(--purple)"/><rect x="3.3" y="4.5" width="5.4" height="3.6" fill="var(--white)"/><rect x="4.3" y="3" width="3.4" height="1.8" fill="var(--white)"/></svg>
        <span>(555) 014-2291</span>
      </li>
      <li>
        <svg class="contact-icon" viewBox="0 0 12 12"><circle cx="6" cy="6" r="6" fill="var(--blue)"/><rect x="3" y="4" width="6" height="4.2" fill="var(--white)"/><path d="M3 4 L6 6.4 L9 4" fill="none" stroke="var(--blue)" stroke-width="0.7"/></svg>
        <span>hello@brightharbor.com</span>
      </li>
      <li>
        <svg class="contact-icon" viewBox="0 0 12 12"><circle cx="6" cy="6" r="6" fill="var(--sky)"/><circle cx="6" cy="6" r="3" fill="none" stroke="var(--white)" stroke-width="0.8"/><path d="M3 6 H9 M6 3 V9" stroke="var(--white)" stroke-width="0.7"/></svg>
        <span>www.brightharborcounseling.com</span>
      </li>
    </ul>

    <footer class="footer-address">
      <svg class="contact-icon" viewBox="0 0 12 12"><circle cx="6" cy="6" r="6" fill="var(--teal)"/><path d="M6 2.6 A2.2 2.2 0 0 1 8.2 4.8 Q8.2 6.4 6 9.3 Q3.8 6.4 3.8 4.8 A2.2 2.2 0 0 1 6 2.6 Z" fill="var(--white)"/><circle cx="6" cy="4.8" r="0.9" fill="var(--teal)"/></svg>
      <span>Bright Harbor Counseling : Suite 214 Harbor Lane, Portland, OR 97204, USA</span>
    </footer>
  </main>
</body>
</html>
```